Business Card Design

We are looking for a business card designed for our landscaping company. We do landscaping installation & Maintenance Services. We would like to see designs that have basic landscaping in background. We also think it is important to have both of our names and phone numbers on the card. We need something that stands out a little whether it is shape of the card or thickness or design.

Business

Bramblewood Yardworks, bramblewoodyard@mailvista.net, Owen Platt 555-273-9104, Daniel Korbin 555-618-3927

```html
<!DOCTYPE html>
<html lang="en">
<head>
<meta charset="utf-8">
<title>Bramblewood Yardworks – Business Card</title>
<link rel="stylesheet" href="https://fonts.googleapis.com/css2?family=Open+Sans:wght@400;600&display=swap">
<style>
  :root {
    --backdrop: #e9e6e1;
    --card-white: #f4f4f6;
    --band-grey: #c4c4c4;
    --band-edge: #d9d9db;
    --accent-red: #e0323f;
    --ink: #141414;
    --ink-soft: #2a2a2a;
  }
  * { margin: 0; padding: 0; box-sizing: border-box; }
  html, body {
    width: 1200px;
    height: 902px;
    overflow: hidden;
    background: var(--backdrop);
    font-family: "Open Sans", Arial, sans-serif;
  }
  .business-card {
    position: absolute;
    left: 100px;
    top: 165px;
    width: 1000px;
    height: 572px;
    background: var(--card-white);
    overflow: hidden;
    box-shadow: 0 10px 30px rgba(0,0,0,0.18);
  }
  .card-swoosh {
    position: absolute;
    inset: 0;
    width: 100%;
    height: 100%;
  }
  .company-name {
    position: absolute;
    left: 62px;
    top: 40px;
    font-size: 58px;
    font-weight: 600;
    letter-spacing: 3px;
    color: var(--ink);
    white-space: nowrap;
  }
  .contact {
    position: absolute;
    color: var(--ink-soft);
    white-space: nowrap;
  }
  .contact-name {
    font-size: 28px;
    letter-spacing: 1px;
    line-height: 1.2;
  }
  .contact-phone {
    display: flex;
    align-items: center;
    gap: 10px;
    margin-left: 26px;
    font-size: 32px;
    letter-spacing: 1px;
    line-height: 1.25;
  }
  .phone-icon { width: 22px; height: 22px; flex: none; }
  .contact--primary { left: 120px; top: 262px; }
  .contact--secondary { left: 590px; top: 142px; }
  .card-email {
    position: absolute;
    left: 400px;
    top: 468px;
    font-size: 24px;
    letter-spacing: 1.5px;
    color: var(--ink-soft);
    white-space: nowrap;
  }
</style>
</head>
<body>
  <div class="business-card">
    <svg class="card-swoosh" viewBox="0 0 1000 572" preserveAspectRatio="none" aria-hidden="true">
      <path d="M30 572 C290 410, 640 280, 1000 228 L1000 572 Z" fill="var(--band-edge)"/>
      <path d="M40 572 C300 420, 650 290, 1000 240" fill="none" stroke="var(--accent-red)" stroke-width="7"/>
      <path d="M70 572 C320 432, 665 304, 1000 254 L1000 572 Z" fill="var(--band-grey)"/>
    </svg>

    <div class="company-name">Bramblewood Yardworks</div>

    <div class="contact contact--secondary">
      <div class="contact-name">Daniel Korbin</div>
      <div class="contact-phone">
        <svg class="phone-icon" viewBox="0 0 22 22" aria-hidden="true">
          <rect width="22" height="22" fill="var(--ink)"/>
          <path d="M7 5 L9.5 5 L10.5 8 L9 9.3 Q10.5 12.5 12.8 13.8 L14 12.3 L17 13.3 L17 15.8 Q15.5 17.3 13 16.5 Q7.5 14 5.5 8.5 Q5 6 7 5 Z" fill="#fff"/>
        </svg>
        <span>555-618-3927</span>
      </div>
    </div>

    <div class="contact contact--primary">
      <div class="contact-name">Owen Platt</div>
      <div class="contact-phone">
        <svg class="phone-icon" viewBox="0 0 22 22" aria-hidden="true">
          <rect width="22" height="22" fill="var(--ink)"/>
          <path d="M7 5 L9.5 5 L10.5 8 L9 9.3 Q10.5 12.5 12.8 13.8 L14 12.3 L17 13.3 L17 15.8 Q15.5 17.3 13 16.5 Q7.5 14 5.5 8.5 Q5 6 7 5 Z" fill="#fff"/>
        </svg>
        <span>555-273-9104</span>
      </div>
    </div>

    <div class="card-email">bramblewoodyard@mailvista.net</div>
  </div>
</body>
</html>
```